Design Project - Finance Website (Only need PSD)

UPDATED PROJECT (Now only PSD needed)
Need a Wordpress design for a company called "Corvale Lending Partners". The company provides finance for corporate clients, businesses and property developers. The design should be business like with appealing colours that communicate trust. I have uploaded a banner and logo to be incorporated or feel free to design something better if you think you can.
** I now only need the PSD
** I want something that is actually designed rather than from a template.
Thanks
Updates
The website will be used for lead generation so the contact form with adjustable fields in the Wordpress backend should be fairly prominent on the page.
I have uploaded a banner and logo for the site. None of the designs I have seen so far were good enough so the first decent design using the new banner and logo provided will win the job. I do not want just a template that has been cut and paste from somewhere else, I want decent design. If anyone provides a decent design then I will give an extra bonus of $150.
Reason: I have uploaded a banner and logo for the site. None of the designs I have seen so far were good enough so the first decent design using the new banner and logo provided will win the job. I do not want just a template that has been cut and paste from somewhere else, I want decent design. If anyone provides a decent design then I will give an extra bonus of $150.
Thanks
Target Market(s)
Business owners & property developers
Industry/Entity Type
Finance
Requirements
Must have
- Contact form on home page that can be altered through the back end eg. ability to add or remove fields. Widgetised sidebars.
Nice to have
- Widgetised footer.

```html
<!DOCTYPE html>
<html lang="en">
<head>
<meta charset="utf-8">
<title>Corvale Lending Partners</title>
<link href="https://fonts.googleapis.com/css2?family=Source+Sans+3:wght@400;600&display=swap" rel="stylesheet">
<style>
:root{
  --page:#fdfdfd;
  --backdrop:#e6e6e6;
  --ink:#2d3335;
  --muted:#3a3f42;
  --brand:#2b95c9;
  --brand-dark:#1a78aa;
  --brand-light:#5fb6e0;
  --panel:#8fc6e6;
  --field:#ffffff;
  --footer-top:#2b2b2b;
  --footer-bottom:#0d0d0d;
  --footer-text:#e8e8e8;
  --footer-faint:#5d5d5d;
}
*{box-sizing:border-box;margin:0;padding:0}
html,body{width:1029px;height:1200px;overflow:hidden}
body{background:var(--backdrop);font-family:"Source Sans 3",sans-serif;color:var(--ink);position:relative}
.page{position:absolute;left:74px;top:0;width:879px;height:1200px;background:var(--page);box-shadow:0 0 12px rgba(0,0,0,.18)}
.abs{position:absolute}

.brand-name{left:45px;top:36px;font-size:31px;line-height:32px;font-weight:600;color:var(--ink);letter-spacing:.5px;white-space:nowrap}
.brand-name span{display:block;font-size:17px;line-height:22px;letter-spacing:3px}

.search{left:516px;top:55px;width:261px;height:40px;background:linear-gradient(var(--brand-light),var(--brand-dark));border-radius:3px;padding:8px 10px}
.search-field{width:208px;height:23px;background:linear-gradient(#fff,#e3e3e3);border-radius:3px}
.search-btn{position:absolute;right:10px;top:8px;width:24px;height:24px}
.social-square{top:60px;width:31px;height:31px;border-radius:3px;background:linear-gradient(#7fc2e6,#2f8fc2);border:1px solid #c9d8e0}

.nav{left:27px;top:127px;width:826px;height:47px;border-radius:8px;background:linear-gradient(#6cc0ea,#1f8bc4);box-shadow:0 0 0 2px #dfe9ee,0 2px 4px rgba(0,0,0,.2);display:flex;align-items:center;justify-content:center}
.nav a{color:#fff;text-decoration:none;font-size:17px;padding:0 18px;border-right:1.5px solid #fff;line-height:18px}
.nav a:last-child{border-right:none}

.hero{left:31px;top:189px;width:820px;height:249px;background:linear-gradient(100deg,#6b6f6c 0%,#9aa3a6 30%,#c6d3da 50%,#7f8a8c 70%,#d8dcd9 100%)}
.hero-caption{left:422px;top:92px;width:383px;height:135px;background:rgba(20,20,20,.72);padding:12px 0 0 20px}
.hero-caption p{color:#fff;font-size:19px;line-height:41px;display:flex;align-items:center;gap:6px;white-space:nowrap}
.step{width:20px;height:20px;background:#fff;color:#222;border-radius:50%;font-size:13px;font-weight:600;display:inline-flex;align-items:center;justify-content:center}
.dots{left:37px;top:218px;display:flex;gap:10px}
.dots i{width:15px;height:15px;border-radius:50%;background:#9ed7f0}
.dots i:first-child{background:#fff}

.welcome-title{left:31px;top:452px;font-size:19px;font-weight:400;color:var(--ink);white-space:nowrap}
.welcome-text{left:34px;top:486px;width:816px;font-size:9.5px;line-height:20.6px;color:var(--muted)}
.btn{border-radius:10px;background:linear-gradient(#58b5e3,#1f88c0);color:#fff;text-align:center;box-shadow:0 0 0 2px #d4e6ef;white-space:nowrap}
.btn-large{left:770px;top:615px;width:69px;height:23px;font-size:10px;line-height:23px}
.btn-small{width:56px;height:18px;font-size:8px;line-height:18px}

.section-title{top:656px;font-size:24px;font-weight:400;color:var(--ink);white-space:nowrap}
.panel{top:692px;height:270px;background:var(--panel);border-radius:6px;box-shadow:0 6px 8px -4px rgba(0,0,0,.25)}

.news-item{left:11px;width:280px;height:72px}
.thumb{position:absolute;left:0;top:0;width:87px;height:71px;border:1px solid #5a8fb5}
.news-item p{position:absolute;left:98px;top:2px;width:172px;font-size:9.5px;line-height:20.6px;color:#1c2427}

.case-image{left:15px;top:19px;width:263px;height:106px}
.case-text{left:15px;top:139px;width:270px;font-size:9.5px;line-height:20.6px;color:#1c2427}

.form-intro{left:14px;top:10px;font-size:9px;color:#2b3d47;white-space:nowrap}
.form-label{left:22px;font-size:8px;color:#3b5566}
.form-field{left:22px;width:188px;height:15px;background:var(--field);border:1px solid #b9c8d1;font-size:7px;color:#b5bcc0;padding-left:5px;line-height:13px}

.footer{left:0;top:1014px;width:879px;height:186px;background:linear-gradient(var(--footer-top),var(--footer-bottom))}
.footer-col h3{font-size:15px;font-weight:600;color:var(--footer-text);margin-bottom:10px;white-space:nowrap}
.footer-col ul{list-style:none;margin-left:2px}
.footer-col li{font-size:12.5px;line-height:15.4px;color:var(--footer-text)}
.footer-name{left:580px;top:50px;width:240px;text-align:center;font-size:26px;line-height:28px;font-weight:600;color:var(--footer-faint);letter-spacing:1px;white-space:nowrap}
.footer-name span{display:block;font-size:16px;line-height:24px;letter-spacing:3px}
.copyright{left:588px;top:124px;width:225px;text-align:center;font-size:11px;color:var(--footer-text);white-space:nowrap}

.side-bar{left:964px;top:480px;width:20px;height:79px;border-radius:4px;background:linear-gradient(90deg,#bdbdbd,#8c8c8c);padding:4px 3px;display:flex;flex-direction:column;gap:5px}
.side-bar i{width:14px;height:14px;border-radius:2px;background:#f2f2f2;opacity:.85}
</style>
</head>
<body>
<div class="page">
  <header>
    <div class="abs brand-name">CORVALE<span>LENDING PARTNERS</span></div>
    <div class="abs search">
      <div class="search-field"></div>
      <svg class="search-btn" viewBox="0 0 24 24" aria-hidden="true"><circle cx="12" cy="12" r="11" fill="#e0553a"/><circle cx="11" cy="11" r="4.5" fill="none" stroke="#fff" stroke-width="2"/><line x1="14" y1="14" x2="17.5" y2="17.5" stroke="#fff" stroke-width="2.2" stroke-linecap="round"/></svg>
    </div>
    <div class="abs social-square" style="left:788px" aria-label="Social profile"></div>
    <div class="abs social-square" style="left:827px" aria-label="Social profile"></div>
    <nav class="abs nav">
      <a href="#">Home</a><a href="#">About Us</a><a href="#">Services</a><a href="#">Finance</a><a href="#">Real Estate</a><a href="#">Products</a><a href="#">Contact Us</a>
    </nav>
  </header>

  <section class="abs hero" role="img" aria-label="Photograph of modern glass office buildings along a city street">
    <div class="abs hero-caption">
      <p><span class="step">1</span>Compare several capital provider rates</p>
      <p><span class="step">2</span>Access to real estate and hedge funds</p>
      <p><span class="step">3</span>Optimise your capital returns</p>
    </div>
    <div class="abs dots"><i></i><i></i><i></i></div>
  </section>

  <h1 class="abs welcome-title">WELCOME TO CORVALE LENDING PARTNERS</h1>
  <p class="abs welcome-text">orem Ipsum is simply dummy text of the printing and typesetting industry. Lorem Ipsum has been the industry's standard dummy text ever since the 1500s, when an unknown printer took a galley of type and scrambled it to make a type specimen book. It has survived not only five centuries, but also the leap into electronic typesetting, remaining essentially unchanged. It was popularised in the 1960s with the release of Typeforge sheets containing Lorem Ipsum passages, and more recently with desktop publishing software like Pagecraft Studio including versions of Lorem Ipsum.is a long established fact that a reader will be distracted by the readable content of a page when looking at its layout. The point of using Lorem Ipsum is that it has a more-or-less normal distribution of letters, as opposed to using 'Content here, content here', making it look like readable English. Many desktop publishing packages and web page editors now use Lorem Ipsum as their default model text, and a search for 'lorem ipsum' will uncover many web sites still in their infancy. Various versions have evolved over the years, sometimes by accident, some-</p>
  <div class="abs btn btn-large">Read more</div>

  <h2 class="abs section-title" style="left:36px">Latest News</h2>
  <h2 class="abs section-title" style="left:339px;top:659px">Case study</h2>
  <h2 class="abs section-title" style="left:640px;top:659px">Contact Form</h2>

  <section class="abs panel" style="left:27px;width:295px">
    <div class="abs news-item" style="top:18px"><div class="thumb" role="img" aria-label="Photo of a glass office tower at dusk" style="background:linear-gradient(#3a5fa8,#1d2a4a)"></div><p>Lorem Ipsum is simply dummy text of the printing and typesetting industry. Lorem Ipsum has been the industry's</p></div>
    <div class="abs news-item" style="top:105px"><div class="thumb" role="img" aria-label="Photo of a modern white and teal office building" style="background:linear-gradient(#3d86c8,#cfe3e4)"></div><p>Lorem Ipsum is simply dummy text of the printing and typesetting industry. Lorem Ipsum has been the industry's</p></div>
    <div class="abs news-item" style="top:192px"><div class="thumb" role="img" aria-label="Photo of a low-rise glass office block" style="background:linear-gradient(#7fb2e0,#d9e3ea)"></div><p>Lorem Ipsum is simply dummy text of the printing and typesetting industry. Lorem Ipsum has been the industry's</p></div>
  </section>

  <section class="abs panel" style="left:329px;width:295px">
    <div class="abs case-image" role="img" aria-label="Photo of a mirrored glass skyscraper reflecting the sky" style="background:linear-gradient(90deg,#2c3e4e,#4c7fb0 45%,#9fc3e4 70%,#3d5266)"></div>
    <p class="abs case-text">Lorem Ipsum is simply dummy text of the printing and typesetting industry. Lorem Ipsum has been the industry's standard dummy text ever since the 1500s, when an unknown printer took a galley of type and scrambled it to</p>
    <div class="abs btn btn-small" style="left:220px;top:242px">Read more</div>
  </section>

  <section class="abs panel" style="left:634px;width:219px">
    <p class="abs form-intro">Fill in your details and we'll get back to you...</p>
    <span class="abs form-label" style="top:41px">Name*</span>
    <div class="abs form-field" style="top:52px">Full name</div>
    <span class="abs form-label" style="top:81px">Phone</span>
    <div class="abs form-field" style="top:90px">Phone Number</div>
    <span class="abs form-label" style="top:119px">Email*</span>
    <div class="abs form-field" style="top:129px">Email address</div>
    <span class="abs form-label" style="top:158px">Message*</span>
    <div class="abs form-field" style="top:168px;height:64px"></div>
    <div class="abs btn btn-small" style="left:148px;top:242px">Submit</div>
  </section>

  <footer class="abs footer">
    <div class="abs footer-col" style="left:37px;top:26px"><h3>Latest News</h3><ul><li>Home</li><li>About Us</li><li>Services</li><li>Finance</li><li>Real Estate</li><li>Contact Us</li></ul></div>
    <div class="abs footer-col" style="left:158px;top:26px"><h3>Case Study</h3><ul style="margin-top:-4px"><li>Home</li><li>About Us</li><li>Services</li><li>Finance</li><li>Real Estate</li><li>Contact Us</li></ul></div>
    <div class="abs footer-col" style="left:265px;top:26px"><h3>Contact</h3><ul><li>Home</li><li>About Us</li><li>Services</li><li>Finance</li><li>Real Estate</li><li>Contact Us</li></ul></div>
    <div class="abs footer-name">CORVALE<span>LENDING PARTNERS</span></div>
    <p class="abs copyright">Copyrights © Corvale All Rights Reserved</p>
  </footer>
</div>
<div class="abs side-bar" aria-label="Social links"><i></i><i></i><i></i><i></i></div>
</body>
</html>
```